TK Stationery - Modern Contemporary

Develop modern template for Letterhead and Stationery (business card, letterhead, envelopes) using the TK Logo and Icon

Colors
0054AA
0677BA
7BADD7
CADEEF
E8F1F8
00AB8E
00BBA5
67D7C9
C6EFE9
E9F9F6
EE7325
F08F49
F5BC92
FAE3D3
FDF4ED
6B429C
8869AF
B7A5CE
E3DAEB
F3F0F8

```html
<!DOCTYPE html>
<html lang="en">
<head>
<meta charset="utf-8">
<title>Tavo Kessa — Business Card</title>
<link rel="stylesheet" href="https://fonts.googleapis.com/css2?family=Bebas+Neue&family=Open+Sans:wght@400&display=swap">
<style>
  :root {
    --backdrop: #9c9c9c;
    --paper: #ffffff;
    --navy: #2b3049;
    --navy-card: #2c304b;
    --green: #1fbf72;
    --orange: #f58634;
    --text-grey: #555a66;
    --name-light: #b9bde6;
  }
  * { margin: 0; padding: 0; box-sizing: border-box; }
  html, body {
    width: 1133px; height: 1200px; overflow: hidden;
    background: var(--backdrop);
  }
  .canvas { position: relative; width: 1133px; height: 1200px; }
  .card {
    position: absolute; left: 196px; width: 734px; height: 417px;
    overflow: hidden;
  }
  .card--front { top: 139px; background: var(--paper); }
  .card--back { top: 641px; background: var(--navy-card); }

  .company-name {
    position: absolute; left: 43px; top: 74px;
    font-family: "Open Sans", Arial, sans-serif;
    font-weight: 400; font-size: 50px; line-height: 1;
    color: var(--navy); white-space: nowrap;
  }

  .address, .contacts {
    position: absolute; left: 43px;
    font-family: "Open Sans", Arial, sans-serif;
    font-size: 16px; color: var(--text-grey); line-height: 20px;
  }
  .address { top: 223px; }
  .contacts { top: 278px; list-style: none; }
  .contacts li { display: flex; align-items: center; height: 21px; white-space: nowrap; }
  .contacts svg { width: 14px; height: 14px; margin-right: 9px; fill: var(--green); flex: none; }

  .person {
    position: absolute; right: 49px; top: 264px; text-align: right;
  }
  .person__name {
    font-family: "Bebas Neue", "Arial Narrow", sans-serif;
    font-size: 38px; color: var(--navy); line-height: 1; letter-spacing: 0.5px;
    white-space: nowrap;
  }
  .person__role {
    font-family: "Open Sans", Arial, sans-serif;
    font-size: 18px; color: var(--orange); line-height: 1; margin-top: 4px;
  }
  .footer-band { position: absolute; left: 0; bottom: 0; width: 734px; height: 21px; }

  .card--back .company-name {
    left: 0; right: 0; top: 172px; text-align: center;
    font-size: 72px; color: var(--name-light);
  }
</style>
</head>
<body>
<main class="canvas">

  <section class="card card--front" aria-label="Business card front">
    <div class="company-name">tavo kessa</div>

    <p class="address">4120 Larkspur Road<br>Fairview, Oregon 97024</p>

    <ul class="contacts">
      <li><svg viewBox="0 0 16 16"><path d="M3.5 1l2.6 3-1.4 1.8c.9 2 2.5 3.6 4.5 4.5L11 8.9l3 2.6-1.2 2.8C7 14 2 9 1.7 3.2z"/></svg>555-214-7730</li>
      <li><svg viewBox="0 0 16 16"><path d="M4 1h8v14H4zM5.5 3v9h5V3zM7 13h2v1H7z" fill-rule="evenodd"/></svg>555-418-2096</li>
      <li><svg viewBox="0 0 16 16"><path d="M1 4h14v9H1zM1.5 4.5L8 9l6.5-4.5v1L8 10 1.5 5.5z" fill-rule="evenodd"/></svg>hello@tavokessa.com</li>
      <li><svg viewBox="0 0 16 16"><circle cx="8" cy="8" r="7"/><path d="M4 5c2 0 2 2 4 2s1 3-1 3-1 3-3 2M10 3c1 1 3 1 3 4" stroke="#fff" stroke-width="1.2" fill="none"/></svg>www.tavokessa.com</li>
    </ul>

    <div class="person">
      <div class="person__name">DANIEL REYES</div>
      <div class="person__role">President</div>
    </div>

    <svg class="footer-band" viewBox="0 0 734 21" aria-hidden="true">
      <polygon points="0,0 379,0 373,21 0,21" fill="var(--navy)"/>
      <polygon points="385,0 734,0 734,21 379,21" fill="var(--green)"/>
    </svg>
  </section>

  <section class="card card--back" aria-label="Business card back">
    <div class="company-name">tavo kessa</div>
  </section>

</main>
</body>
</html>
```